Thoroughbred Racing Partnership needs web design

Glimmer of Laurel Partners is a management group who buys horses and races them on both the West and East coasts. The premise of the business is for an investment as little as $500, anyone can be a partner and own a percentage of a horse(s). This is a low cost way of getting involved in the exciting sport of Thoroughbred Racing, without shouldering the heavy financial responsibility. Our target market is mostly males 40+ but we want to include all target markets. We are looking for something very clean and professional, we want to give an image of success. Nothing overly "artsy." I have included the logo in which you can incorporate in the site. Also, the logo colors will be the colors of our "silks." The silks are what the jockey wears and will be an important marketing tool for GOL. We would like a very prominent picture of a racehorse somewhere on the homepage, we want to make it clear that is a website for Horseracing partnerships.

On the top of the site, it should say "Glimmer of Laurel" (on the top)
and below that "Thoroughbred Racing Partnerships." (below that)

The main sections, which should be across the top are:

Home
About Us
Ownership
Stable Roster
News
Contact us

Some of these will have drop down menus.

An example of a competitor website that we like is: www.harrowgatefarm.example
An example of a competitor website that we don't like is: www.paddockvue.example
Updates

Project Deadline Extended
Reason: We have a Board of Directors meeting on the 22nd and we will be making a decision on that day. I'm giving an extension so that all designers are able to submit their designs by the 22nd. Thank you!

Target Market(s)

40+ males

Industry/Entity Type

Business

Requirements
Must have
• our logo must be on the site. We would like at least one bold image of a thoroughbred horse in action. The picture is going to tell the story so it needs to be very eye-catching.

Our slogan should also be included on the website, "Experience the thrill of owning a Racehorse."
Should not have
• cartoons, artsy pictures, pictures of Steeplechase horses or "jumpers." This partnership is for racehorses only, there is not jumping involved with the horses.

```html
<!DOCTYPE html>
<html lang="en">
<head>
<meta charset="utf-8">
<title>Glimmer of Laurel Partners</title>
<link href="https://fonts.googleapis.com/css2?family=Montserrat:wght@400;600;700&family=Arimo:wght@400&display=swap" rel="stylesheet">
<style>
  :root {
    --navy: #0f2a5a;
    --brand-blue: #1a4a7a;
    --bar-blue: #1f5f8f;
    --bar-edge: #174c75;
    --sky-top: #8cc3e8;
    --sky-bottom: #c9e4f5;
    --phone-text: #8fb8d8;
    --social: #a9cbe4;
    --button-top: #1d5595;
    --button-bottom: #0b2f62;
    --body-text: #2a2a2a;
    --footer-bg: #dcdcdc;
    --footer-title: #a6a6a6;
    --footer-logo: #9a9a9a;
    --white: #ffffff;
  }
  * { margin: 0; padding: 0; box-sizing: border-box; }
  html, body { width: 1200px; height: 879px; overflow: hidden; background: var(--white); }
  body { position: relative; font-family: "Montserrat", sans-serif; }

  .hero {
    position: absolute; left: 0; top: 0; width: 1200px; height: 477px;
    background: linear-gradient(180deg, var(--sky-top) 0%, var(--sky-bottom) 100%);
    overflow: hidden;
  }
  .hero-photo {
    position: absolute; left: 0; top: 69px; width: 720px; height: 408px;
    background:
      linear-gradient(90deg, rgba(201,228,245,0) 70%, rgba(170,210,238,1) 100%),
      linear-gradient(180deg, #5d7a5a 0%, #6f6a4c 30%, #7a4a2c 55%, #9b8a70 85%, #b2a58c 100%);
  }
  .top-bar {
    position: absolute; left: 0; top: 0; width: 1200px; height: 69px;
    background: var(--bar-blue); border-bottom: 2px solid var(--bar-edge);
  }
  .logo-tab { position: absolute; left: 0; top: 0; }
  .site-logo {
    position: absolute; left: 196px; top: 46px;
    display: flex; align-items: center; gap: 9px; white-space: nowrap;
    font-weight: 700; font-size: 26px; line-height: 32px; color: var(--brand-blue); letter-spacing: 0.3px;
  }
  .site-logo .mark { width: 16px; height: 16px; border-radius: 50%; background: var(--brand-blue); flex: none; }

  .social { position: absolute; top: 23px; left: 665px; display: flex; gap: 3px; }
  .social span { width: 30px; height: 30px; border-radius: 50%; background: var(--social); display: block; }
  .bar-divider { position: absolute; left: 824px; top: 8px; width: 1px; height: 52px; background: rgba(255,255,255,0.2); }
  .phone { position: absolute; left: 850px; top: 24px; display: flex; align-items: center; gap: 10px;
    font-weight: 600; font-size: 22px; color: var(--phone-text); }

  .main-nav { position: absolute; top: 88px; left: 0; width: 1200px; }
  .main-nav a { position: absolute; color: var(--white); text-decoration: none; font-size: 12px; font-weight: 600; white-space: nowrap; }
  .main-nav .has-menu::after { content: "▾"; margin-left: 8px; font-size: 12px; }

  .tagline { position: absolute; right: 167px; top: 202px; text-align: right; }
  .tagline h1 { font-size: 40px; font-weight: 700; color: var(--brand-blue); line-height: 1.1; white-space: nowrap; }
  .tagline p { font-size: 17px; font-weight: 600; color: var(--white); margin-top: 6px; }
  .cta {
    position: absolute; left: 733px; top: 294px; width: 299px; height: 64px; border-radius: 8px;
    background: linear-gradient(180deg, var(--button-top), var(--button-bottom));
    box-shadow: 0 3px 6px rgba(0,0,0,0.3);
    display: flex; align-items: center; justify-content: space-between; padding: 0 24px;
    color: var(--white); font-weight: 600; font-size: 17px; text-decoration: none;
  }

  .intro { position: absolute; left: 173px; top: 514px; width: 560px; }
  .intro h2 { font-size: 24px; line-height: 30px; font-weight: 600; color: var(--navy); letter-spacing: -0.6px; white-space: nowrap; }
  .intro p { width: 532px; font-family: "Arimo", sans-serif; font-size: 11px; line-height: 19px; color: var(--body-text); margin-top: 10px; padding-left: 2px; }
  .read-more { position: absolute; left: 601px; top: 626px; font-size: 14px; font-weight: 600; color: var(--navy); text-decoration: underline; }

  .photo-card {
    position: absolute; left: 744px; top: 437px; width: 338px; height: 228px;
    background: var(--white); border-radius: 5px; padding: 9px;
    box-shadow: 0 4px 14px rgba(0,0,0,0.18);
  }
  .photo-card .photo {
    width: 100%; height: 100%;
    background: linear-gradient(180deg, #7b6a5c 0%, #6b4328 45%, #5f7f3f 80%, #6f9a4a 100%);
  }

  .site-footer {
    position: absolute; left: 0; top: 714px; width: 1200px; height: 165px;
    background: var(--footer-bg); box-shadow: inset 0 4px 6px -3px rgba(0,0,0,0.2);
  }
  .sitemap { position: absolute; left: 176px; top: 59px; }
  .sitemap h3, .contact h3 { font-size: 17px; font-weight: 600; color: var(--footer-title); }
  .sitemap ul { list-style: none; display: grid; grid-template-columns: 97px 95px 80px; row-gap: 4px; margin-top: 10px; }
  .sitemap a { font-family: "Arimo", sans-serif; font-size: 11px; color: var(--body-text); text-decoration: none; }
  .contact { position: absolute; right: 368px; top: 61px; text-align: right; }
  .contact p { font-family: "Arimo", sans-serif; font-size: 11px; line-height: 18px; color: var(--body-text); margin-top: 8px; }
  .footer-logo { position: absolute; left: 872px; top: 66px; font-size: 30px; font-weight: 700; color: var(--footer-logo); white-space: nowrap; }
</style>
</head>
<body>
  <section class="hero">
    <div class="hero-photo" role="img" aria-label="Two thoroughbred racehorses with jockeys in red and white silks galloping down the track, tote board behind"></div>

    <header class="top-bar"></header>
    <svg class="logo-tab" width="530" height="130" viewBox="0 0 530 130" aria-hidden="true">
      <path d="M0 7 L88 7 C120 7 138 30 158 65 C178 100 195 127 250 127 L300 127 C355 127 380 100 410 65 C440 30 470 7 515 7 L530 7 L530 0 L0 0 Z" fill="#1f5f8f"/>
      <path d="M88 7 C120 7 138 30 158 65 C178 100 195 127 250 127 L300 127 C355 127 380 100 410 65 C440 30 470 7 515 7 Z" fill="#ffffff"/>
      <path d="M482 69 L487 79 L495 69 Z" fill="#1f5f8f"/>
    </svg>
    <div class="site-logo"><span class="mark"></span>GOL Partners</div>

    <div class="social" aria-label="Social links">
      <span></span><span></span><span></span><span></span>
    </div>
    <div class="bar-divider"></div>
    <div class="phone">
      <svg width="26" height="26" viewBox="0 0 24 24" aria-hidden="true"><path fill="#8fb8d8" d="M6.6 10.8c1.4 2.8 3.8 5.1 6.6 6.6l2.2-2.2c.3-.3.7-.4 1-.2 1.1.4 2.3.6 3.6.6.6 0 1 .4 1 1V20c0 .6-.4 1-1 1C10.6 21 3 13.4 3 4c0-.6.4-1 1-1h3.5c.6 0 1 .4 1 1 0 1.3.2 2.5.6 3.6.1.3 0 .7-.2 1z"/></svg>
      1800-555 0142
    </div>

    <nav class="main-nav">
      <a href="#" style="left:465px">HOME</a>
      <a href="#" class="has-menu" style="left:548px">ABOUT US</a>
      <a href="#" style="left:648px">OWNERSHIP</a>
      <a href="#" class="has-menu" style="left:751px">STABLE ROSTER</a>
      <a href="#" style="left:898px">NEWS</a>
      <a href="#" style="left:979px">CONTACT US</a>
    </nav>

    <div class="tagline">
      <h1>Glimmer of Laurel</h1>
      <p>Thoroughbred Racing Partnerships.</p>
    </div>
    <a class="cta" href="#">Learn About Partnerships
      <svg width="16" height="24" viewBox="0 0 16 24" aria-hidden="true"><path d="M3 3 L12 12 L3 21" fill="none" stroke="#ffffff" stroke-width="4"/></svg>
    </a>
  </section>

  <section class="intro">
    <h2>Experience the thrill of owning a Racehorse.</h2>
    <p>Lorem ipsum dolor sit amet, consectetur adipiscing elit. Donec eleifend diam id vulputate dictum. Morbi sagittis dui sit amet ultricies pharetra. Vestibulum sagittis turpis a fermentum interdum. Mauris sapien arcu, sollicitudin at diam eget, posuere lobortis turpis. Morbi nisi odio, congue eu leo a, sollicitudin congue leo.</p>
  </section>
  <a class="read-more" href="#">READ MORE</a>

  <figure class="photo-card">
    <div class="photo" role="img" aria-label="Pack of racehorses with jockeys galloping on a turf course"></div>
  </figure>

  <footer class="site-footer">
    <div class="sitemap">
      <h3>Sitemap</h3>
      <ul>
        <li><a href="#">Home</a></li>
        <li><a href="#">Stable Roster</a></li>
        <li><a href="#">Ownership</a></li>
        <li><a href="#">About Us</a></li>
        <li><a href="#">News</a></li>
        <li><a href="#">Contact us</a></li>
      </ul>
    </div>
    <div class="contact">
      <h3>GOL Partners</h3>
      <p>Lorem ipsum Street it amet, consectetur adipiscing elit. Donec<br>P: 1800 - 555 0142, E: email@golpartners.example</p>
    </div>
    <div class="footer-logo">GOL Partners</div>
  </footer>
</body>
</html>
```